Membership Based Medical Practice Website

We need a functioning website for a new Membership based medical practice. There will be an enrollment fee and a monthly fee. We would like to see designs that are modern, simple. Should use neutral light colors. Examples of sites we like are www.kellanmoorclinic.com and https://fernholtcare.com/ We also have a link that when "Join Now" is clicked it will go to the signup website.

Target Market(s)

Gay Men, local population, Age group 20 to 60's.

Industry/Entity Type

Medical

Coding

Coded - Design and coding required

Number of Pages Required

5+ page

Font styles to use
Sans Serif

Colors
ffffff
cee9f5
ecf7fb
cfeae6
edf8f6
aaaaaa
e9e9e9
dbdbdb
fff3d1

Requirements
Must have
• Logo and header on every page. Clean, simple design, clear content, mobile compatible.
• Must use Wordpress
Nice to have
• Ideas should come from kellanmoorclinic.com
• Easy to read
Should not have
• Generic patient pictures, bold colors.
• Should not copy from above websites.

```html
<!DOCTYPE html>
<html lang="en">
<head>
<meta charset="utf-8">
<title>Harrowfield Infectious Disease Specialists</title>
<link href="https://fonts.googleapis.com/css2?family=Montserrat:wght@300;400;500;600&family=Open+Sans:wght@400;600&display=swap" rel="stylesheet">
<style>
:root{
  --ink:#3f3f3f;
  --text:#555555;
  --muted:#777777;
  --teal:#cfeae6;
  --teal-soft:#edf8f6;
  --tick:#9fd3cc;
  --white:#ffffff;
  --footer:#a5a5a5;
  --line:#dbdbdb;
}
*{box-sizing:border-box;margin:0;padding:0}
html,body{width:1200px;height:3644px;overflow:hidden;background:var(--white)}
body{position:relative;font-family:"Open Sans",Arial,sans-serif;color:var(--text)}
.abs{position:absolute}
.heading{font-family:"Montserrat",Arial,sans-serif;font-weight:300;color:var(--ink);text-align:center;line-height:1.5}

/* header */
.site-header{position:absolute;left:0;top:0;width:1200px;height:100px;background:var(--white);z-index:3}
.brand-disc{position:absolute;left:84px;top:-60px;width:260px;height:268px;border-radius:50%;background:var(--white);z-index:4;display:flex;flex-direction:column;align-items:center;justify-content:flex-end;padding-bottom:52px}
.brand-name{font-family:"Montserrat",Arial,sans-serif;font-weight:400;color:#8a8a8a;text-align:center;font-size:14px;letter-spacing:6px;line-height:1.2}
.brand-name small{display:block;font-size:10.5px;letter-spacing:1px;margin-top:2px}
.nav{position:absolute;left:466px;top:40px;display:flex;gap:28px;font-family:"Montserrat",Arial,sans-serif;font-size:14px;color:#666;z-index:4}
.join{position:absolute;left:988px;top:28px;width:100px;height:46px;border-radius:23px;background:var(--teal);font-family:"Montserrat",Arial,sans-serif;font-size:14px;font-weight:500;color:#444;display:flex;align-items:center;justify-content:center;z-index:4}

/* hero */
.hero{position:absolute;left:0;top:100px;width:1200px;height:558px;background:linear-gradient(180deg,#ece3f0 0%,#e2cbd6 45%,#e0a98a 72%,#b47a5c 100%)}
.hero-title{position:absolute;left:0;top:160px;width:1200px;font-size:40px;color:#555}

/* services */
.intro-title{position:absolute;left:0;top:748px;width:1200px;font-size:34px}
.intro-sub{position:absolute;left:0;top:886px;width:1200px;text-align:center;font-size:18px;color:#666}
.conditions{position:absolute;list-style:none;font-size:17px;font-weight:600;color:#444}
.conditions li{height:42.5px;display:flex;align-items:center;gap:14px}
.tick{width:16px;height:16px;flex:none}

/* why */
.why{position:absolute;left:0;top:1288px;width:1200px;height:1040px;background:var(--teal-soft)}
.why-title{position:absolute;left:0;top:1368px;width:1200px;font-size:34px}
.feature{position:absolute;width:240px;text-align:center}
.feature-icon{width:100px;height:90px;margin:0 auto;border-radius:14px;background:linear-gradient(160deg,#e3eeec,#d3e2df)}
.feature h3{font-family:"Montserrat",Arial,sans-serif;font-weight:300;font-size:22px;color:#444;line-height:1.5;margin-top:20px}
.feature p{font-size:13.5px;line-height:1.9;color:#555;margin-top:16px}

/* pricing */
.pricing-title{position:absolute;left:0;top:2440px;width:1200px;font-size:34px}
.pricing-sub{position:absolute;left:0;top:2508px;width:1200px;text-align:center;font-family:"Montserrat",Arial,sans-serif;font-weight:300;font-size:22px;color:#444}
.pricing-sub b{font-weight:300;font-size:30px}
.perks{position:absolute;left:110px;top:2620px;width:420px;list-style:none;font-size:15.5px;line-height:1.8;color:#555}
.perks li{display:flex;gap:16px;margin-bottom:22px}
.perks .tick{margin-top:6px;width:14px;height:14px}
.perks-photo{position:absolute;left:603px;top:2610px;width:486px;height:318px;background:linear-gradient(135deg,#556b78 0%,#8ea1ad 45%,#b5282c 78%,#3b2b2a 100%)}
.learn{position:absolute;left:469px;top:3024px;width:262px;height:62px;border-radius:31px;background:var(--teal);font-family:"Montserrat",Arial,sans-serif;font-weight:600;font-size:15px;color:#3f3f3f;display:flex;align-items:center;justify-content:center}

/* footer */
.site-footer{position:absolute;left:0;top:3208px;width:1200px;height:436px;background:var(--footer);color:var(--white)}
.footer-brand{position:absolute;left:108px;top:196px;width:275px;font-family:"Montserrat",Arial,sans-serif;font-weight:400;color:var(--white);text-align:center;font-size:17px;letter-spacing:9px;line-height:1.3}
.footer-brand small{display:block;font-size:12.5px;letter-spacing:1px}
.footer-col h4{font-family:"Montserrat",Arial,sans-serif;font-weight:400;font-size:18px;margin-bottom:22px}
.footer-col{position:absolute;top:88px;font-size:13.5px}
.links{list-style:none;line-height:25px}
.newsletter p{line-height:1.7;width:230px}
.email-field{width:256px;height:34px;background:var(--white);margin-top:18px;color:#777;font-size:12px;padding:9px 10px}
.subscribe{width:146px;height:48px;border-radius:24px;background:var(--teal);color:#333;font-family:"Montserrat",Arial,sans-serif;font-weight:600;font-size:14px;display:flex;align-items:center;justify-content:center;margin-top:14px}
.contact-row{display:flex;gap:22px;margin-bottom:20px;line-height:1.6}
.contact-row svg{flex:none;width:14px;height:14px;margin-top:3px}
.footer-rule{position:absolute;left:108px;top:335px;width:984px;height:1px;background:#bdbdbd}
.copyright{position:absolute;left:110px;top:374px;font-size:13px}
.social{position:absolute;top:364px;width:36px;height:36px;border:1.5px solid var(--white);border-radius:50%}
</style>
</head>
<body>

<header class="site-header">
  <nav class="nav">
    <span>HOME</span><span>SPECIALTIES</span><span>PRICING</span><span>ABOUT US</span><span>FAQ</span><span>BLOG</span>
  </nav>
  <a class="join">JOIN US</a>
</header>
<div class="brand-disc">
  <div class="brand-name">HARROWFIELD<small>INFECTIOUS DISEASE SPECIALISTS</small></div>
</div>

<section class="hero" role="img" aria-label="Photo of four friends with arms around each other, facing a sunset over hills"></section>
<h1 class="heading hero-title">Specialty medicine with<br>Commitment, Compassion and Care</h1>

<h2 class="heading intro-title">We offer comprehensive treatment of a wide<br>Variety of infectious diseases.</h2>
<p class="intro-sub">Out expertise is in the following area.</p>

<ul class="conditions" style="left:258px;top:963px">
  <li><svg class="tick" viewBox="0 0 16 16"><circle cx="8" cy="8" r="8" fill="#cfeae6"/><path d="M4.5 8.2l2.3 2.3 4.7-4.8" stroke="#7fbfb6" stroke-width="1.6" fill="none"/></svg>HIV/PrEP</li>
  <li><svg class="tick" viewBox="0 0 16 16"><circle cx="8" cy="8" r="8" fill="#cfeae6"/><path d="M4.5 8.2l2.3 2.3 4.7-4.8" stroke="#7fbfb6" stroke-width="1.6" fill="none"/></svg>Chronic Hepatitis</li>
  <li><svg class="tick" viewBox="0 0 16 16"><circle cx="8" cy="8" r="8" fill="#cfeae6"/><path d="M4.5 8.2l2.3 2.3 4.7-4.8" stroke="#7fbfb6" stroke-width="1.6" fill="none"/></svg>Sexually transmitted infections</li>
  <li><svg class="tick" viewBox="0 0 16 16"><circle cx="8" cy="8" r="8" fill="#cfeae6"/><path d="M4.5 8.2l2.3 2.3 4.7-4.8" stroke="#7fbfb6" stroke-width="1.6" fill="none"/></svg>Pre-travel vaccinations and counselling</li>
  <li><svg class="tick" viewBox="0 0 16 16"><circle cx="8" cy="8" r="8" fill="#cfeae6"/><path d="M4.5 8.2l2.3 2.3 4.7-4.8" stroke="#7fbfb6" stroke-width="1.6" fill="none"/></svg>Infections associated with medical devices</li>
</ul>
<ul class="conditions" style="left:696px;top:963px">
  <li><svg class="tick" viewBox="0 0 16 16"><circle cx="8" cy="8" r="8" fill="#cfeae6"/><path d="M4.5 8.2l2.3 2.3 4.7-4.8" stroke="#7fbfb6" stroke-width="1.6" fill="none"/></svg>Bone and Joint infections</li>
  <li><svg class="tick" viewBox="0 0 16 16"><circle cx="8" cy="8" r="8" fill="#cfeae6"/><path d="M4.5 8.2l2.3 2.3 4.7-4.8" stroke="#7fbfb6" stroke-width="1.6" fill="none"/></svg>Postsurgical infections</li>
  <li><svg class="tick" viewBox="0 0 16 16"><circle cx="8" cy="8" r="8" fill="#cfeae6"/><path d="M4.5 8.2l2.3 2.3 4.7-4.8" stroke="#7fbfb6" stroke-width="1.6" fill="none"/></svg>Diabetes related infections</li>
  <li><svg class="tick" viewBox="0 0 16 16"><circle cx="8" cy="8" r="8" fill="#cfeae6"/><path d="M4.5 8.2l2.3 2.3 4.7-4.8" stroke="#7fbfb6" stroke-width="1.6" fill="none"/></svg>Tuberculosis</li>
</ul>

<section class="why"></section>
<h2 class="heading why-title">Less wait, more personal.<br>We are not your traditional doctor’s office.</h2>

<div class="feature" style="left:89px;top:1560px"><div class="feature-icon" role="img" aria-label="Line icon of a rising bar chart"></div><h3>Straightforward<br>pricing</h3><p>We charge all our patients the same low rate - no surprises.</p></div>
<div class="feature" style="left:349px;top:1560px"><div class="feature-icon" role="img" aria-label="Line icon of a calendar with a plus sign"></div><h3>Available when<br>you are</h3><p>New patient appointments are available within 1 week.</p></div>
<div class="feature" style="left:611px;top:1560px"><div class="feature-icon" role="img" aria-label="Line icon of a calendar with a check mark"></div><h3>Hassle-free<br>booking</h3><p>Schedule your appointment online at your convenience - no need to call during business hours.</p></div>
<div class="feature" style="left:871px;top:1560px"><div class="feature-icon" role="img" aria-label="Line icon of a hand holding a heart"></div><h3>Devoted<br>care</h3><p>We schedule enough time at each visit to make sure all of your questions are answered.</p></div>

<div class="feature" style="left:89px;top:1908px"><div class="feature-icon" role="img" aria-label="Line icon of a doctor on a computer screen"></div><h3>Within your<br>reach</h3><p>Follow-up appointments may be done by video chat for your convenience.</p></div>
<div class="feature" style="left:349px;top:1908px"><div class="feature-icon" role="img" aria-label="Line icon of a microscope"></div><h3>Save on lab<br>costs</h3><p>If paying upfront for labs, we offer discounted pricing of up to 90% off standard rates.</p></div>
<div class="feature" style="left:611px;top:1908px"><div class="feature-icon" role="img" aria-label="Line icon of a mortar and pestle"></div><h3>Save on<br>medications</h3><p>We offer deeply discounted wholesale price medications for our members at pharmacy on site.</p></div>
<div class="feature" style="left:871px;top:1908px"><div class="feature-icon" role="img" aria-label="Line icon of a document"></div><h3>No middle<br>man</h3><p>We don;t bill any insurance plans so decisions about your healthcare will be made by you and Dr. Ellery, without the impersonal management that comes from third-party payers.</p></div>

<h2 class="heading pricing-title">Our pricing is simple, transparent and affordable.</h2>
<p class="pricing-sub">Membership Plan <b>$80/mo</b>, plus a one-time <b>$99</b> enrollment fee.</p>

<ul class="perks">
  <li><svg class="tick" viewBox="0 0 16 16"><circle cx="8" cy="8" r="8" fill="#cfeae6"/><path d="M4.5 8.2l2.3 2.3 4.7-4.8" stroke="#7fbfb6" stroke-width="1.6" fill="none"/></svg><span>Includes all appointments, no co-pay</span></li>
  <li><svg class="tick" viewBox="0 0 16 16"><circle cx="8" cy="8" r="8" fill="#cfeae6"/><path d="M4.5 8.2l2.3 2.3 4.7-4.8" stroke="#7fbfb6" stroke-width="1.6" fill="none"/></svg><span>Relaxed, unrushed visits</span></li>
  <li><svg class="tick" viewBox="0 0 16 16"><circle cx="8" cy="8" r="8" fill="#cfeae6"/><path d="M4.5 8.2l2.3 2.3 4.7-4.8" stroke="#7fbfb6" stroke-width="1.6" fill="none"/></svg><span>Direct communication with your doctor via phone, email, video chat 24/7</span></li>
  <li><svg class="tick" viewBox="0 0 16 16"><circle cx="8" cy="8" r="8" fill="#cfeae6"/><path d="M4.5 8.2l2.3 2.3 4.7-4.8" stroke="#7fbfb6" stroke-width="1.6" fill="none"/></svg><span>Convenient online scheduling (no need to call during business hours)</span></li>
  <li><svg class="tick" viewBox="0 0 16 16"><circle cx="8" cy="8" r="8" fill="#cfeae6"/><path d="M4.5 8.2l2.3 2.3 4.7-4.8" stroke="#7fbfb6" stroke-width="1.6" fill="none"/></svg><span>Wholesale price for labs and medications</span></li>
</ul>
<div class="perks-photo" role="img" aria-label="Photo of a hand in a red sleeve holding an enamel camping mug outdoors"></div>
<a class="learn">LEARN MORE ABOUT US</a>

<footer class="site-footer">
  <div class="footer-brand">HARROWFIELD<small>INFECTIOUS DISEASE SPECIALISTS</small></div>

  <div class="footer-col" style="left:411px">
    <h4>Information</h4>
    <ul class="links"><li>Help</li><li>FAQ</li><li>Support</li><li>Sitemap</li><li>Terms Of Use</li><li>Privacy Statement</li></ul>
  </div>

  <div class="footer-col newsletter" style="left:586px">
    <h4>Newsletter Subscription</h4>
    <p>Register your Email Address to get Information about us</p>
    <div class="email-field">Email Address</div>
    <div class="subscribe">SUBSCRIBE</div>
  </div>

  <div class="footer-col" style="left:887px">
    <h4>Contact Us</h4>
    <div class="contact-row"><svg viewBox="0 0 14 14"><path d="M7 1a4 4 0 0 0-4 4c0 3 4 8 4 8s4-5 4-8a4 4 0 0 0-4-4zm0 5.5A1.5 1.5 0 1 1 7 3.5a1.5 1.5 0 0 1 0 3z" fill="#fff"/></svg><span>Suite 4, 218 Larkspur Row<br>Brenmoor Valley</span></div>
    <div class="contact-row"><svg viewBox="0 0 14 14"><path d="M3 1.5l2.2 2.4-1.2 1.6a8 8 0 0 0 4.5 4.5l1.6-1.2 2.4 2.2-1.4 1.7C6 12.5 1.5 8 1.3 2.9z" fill="#fff"/></svg><span>+1 555 010 4477</span></div>
    <div class="contact-row"><svg viewBox="0 0 14 14"><rect x="1" y="4" width="12" height="8" rx="1" fill="#fff"/><rect x="4" y="1.5" width="6" height="3" fill="#fff"/></svg><span>+1 555 010 2290</span></div>
    <div class="contact-row"><svg viewBox="0 0 14 14"><rect x="1" y="3" width="12" height="8" fill="#fff"/><path d="M1 3l6 5 6-5" stroke="#a5a5a5" stroke-width="1.2" fill="none"/></svg><span>info@harrowfieldid.com</span></div>
  </div>

  <div class="footer-rule"></div>
  <p class="copyright">Copyrights © 2019, Harrowfield. All rights reserved.</p>
  <span class="social" style="left:966px"></span>
  <span class="social" style="left:1010px"></span>
  <span class="social" style="left:1054px"></span>
</footer>

</body>
</html>
```